High end Desks & Chairs Distibutor looking for a brochure desin

Brightmoor Works G.P, Canadian Furniture and Stationery Distributor, (very attractive patented design -mainly Desks & Chairs-), Adjstable to fit many needs.
3 folds flyer,
Bilangual text and photos provided,
Use same colors as Logo
Flyer Disign shoul reflect Ergonomy, High End User Freindly Products, Eco Freindly materials,

Target Market(s)

Limited mobility people
Children from 4 to 17 years old
Multi porpuses desks users

Industry/Entity Type

Distributor

Requirements
Nice to have
• Have a hint for Ergonomic, Adjustable, multi-purpose use.

```html
<!DOCTYPE html>
<html lang="en">
<head>
<meta charset="utf-8">
<title>Brightmoor Works G.P – Tri-fold Brochure</title>
<link rel="stylesheet" href="https://fonts.googleapis.com/css2?family=Roboto+Condensed:wght@400;700&family=Roboto:wght@400;500;700&display=swap">
<style>
  :root{
    --red:#f20c0c;
    --red-deep:#d60000;
    --ink:#1b1b1b;
    --grey:#5a5a5a;
    --paper:#ffffff;
    --mist:#eeeeee;
    --photo-wood:#d9b98a;
    --photo-white:#e7e9ec;
  }
  *{margin:0;padding:0;box-sizing:border-box}
  html,body{width:1200px;height:907px;overflow:hidden;background:var(--paper)}
  body{font-family:"Roboto",Arial,sans-serif;color:var(--ink);position:relative}

  .brochure{position:absolute;left:115px;top:100px;width:983px;height:700px;background:var(--paper);overflow:hidden;outline:1px solid #e2e2e2}
  .backdrop{position:absolute;left:0;top:0;width:660px;height:520px;background:linear-gradient(180deg,#fafafa 0%,#f0f0f0 60%,#f7f7f7 100%)}
  .shapes{position:absolute;left:0;top:0;width:983px;height:700px}
  .fold{position:absolute;top:0;width:1px;height:700px;background:rgba(0,0,0,.06)}

  /* left panel */
  .feature{position:absolute;top:52px;width:160px;text-align:center}
  .feature .badge{display:block;width:52px;height:52px;margin:0 auto 9px;border-radius:50%;background:var(--red);border:3px solid #fff;box-shadow:0 0 0 2px var(--red)}
  .feature .badge svg{width:52px;height:52px}
  .feature h3{font-family:"Roboto Condensed",Arial,sans-serif;font-weight:700;font-size:17px;line-height:1;color:var(--ink)}
  .feature p{font-size:10px;line-height:1.2;color:var(--ink);text-transform:uppercase}
  .feature--quality{left:8px}
  .feature--eco{left:172px}
  .feature--eco h3{font-size:19px}

  .about-title{position:absolute;left:25px;top:171px;font-family:"Roboto Condensed",Arial,sans-serif;font-weight:700;font-size:24px;color:var(--red)}
  .about-list{position:absolute;left:32px;top:220px;width:260px;list-style:none;font-size:11px;line-height:1.3}
  .about-list li{position:relative;padding-left:12px;margin-bottom:10px}
  .about-list li::before{content:"";position:absolute;left:0;top:5px;width:6px;height:6px;border-radius:50%;background:var(--red)}

  .photo{position:absolute}
  .photo--standing-desk{left:55px;top:345px;width:270px;height:340px;background:linear-gradient(180deg,var(--photo-wood) 0%,#e8d2b0 30%,#eeeeee 55%,#dcdcdc 100%);border-radius:6px}
  .photo--study-desk{left:670px;top:135px;width:295px;height:235px;background:linear-gradient(180deg,#f4f5f6 0%,var(--photo-white) 50%,#c9ccd1 100%);border-radius:6px}

  /* middle panel */
  .brand{position:absolute;display:flex;align-items:center;gap:8px}
  .brand .dot{border-radius:50%;background:var(--red);flex:none}
  .brand .name{font-family:"Roboto Condensed",Arial,sans-serif;font-weight:700;color:#333;white-space:nowrap;line-height:1}
  .brand .tag{display:block;font-family:"Roboto Condensed",Arial,sans-serif;font-weight:400;color:#333;text-transform:uppercase;white-space:nowrap;margin-top:3px}
  .brand--middle{left:415px;top:172px}
  .brand--middle .dot{width:22px;height:22px}
  .brand--middle .name{font-size:16px}
  .brand--middle .tag{font-size:5.5px}
  .brand--cover{left:692px;top:50px}
  .brand--cover .dot{width:40px;height:40px}
  .brand--cover .name{font-size:25px}
  .brand--cover .tag{font-size:8px}

  .claim{position:absolute;left:372px;top:315px;width:250px;height:250px;border-radius:50%;background:var(--paper);display:flex;flex-direction:column;align-items:center;justify-content:center;text-align:center;color:var(--ink)}
  .claim span{display:block;line-height:1.1}
  .claim .c1{font-family:"Roboto Condensed",Arial,sans-serif;font-weight:700;font-size:28px}
  .claim .c2{font-size:28px;font-weight:400}
  .claim .c3{font-family:"Roboto",Arial,sans-serif;font-weight:700;font-size:24px;letter-spacing:3px}
  .claim .c4{font-family:"Roboto Condensed",Arial,sans-serif;font-weight:700;font-size:28px}

  .phone{position:absolute;left:335px;top:597px;width:325px;text-align:center;font-family:"Roboto Condensed",Arial,sans-serif;font-weight:700;font-size:36px;color:#fff}
  .web{position:absolute;top:644px;text-align:center;font-size:13.5px;letter-spacing:2.6px;color:#fff}
  .web--middle{left:335px;width:325px}
  .web--cover{left:660px;width:323px}

  /* cover panel */
  .cover-title{position:absolute;left:660px;top:452px;width:323px;text-align:center;font-family:"Roboto Condensed",Arial,sans-serif;font-weight:700;line-height:1}
  .cover-title .l1{display:block;font-size:56px;color:var(--ink);letter-spacing:-.5px}
  .cover-title .l2{display:block;font-size:50px;color:#fff;margin-top:8px}
  .cover-title .l3{display:block;font-family:"Roboto Condensed",Arial,sans-serif;font-weight:400;font-size:24px;color:#fff;margin-top:6px}
</style>
</head>
<body>
<main class="brochure">
  <div class="backdrop" role="img" aria-label="Faded photo of a bright modern interior"></div>

  <svg class="shapes" viewBox="0 0 983 700" aria-hidden="true">
    <defs>
      <linearGradient id="rule" x1="0" x2="1">
        <stop offset="0" stop-color="#111"/>
        <stop offset="1" stop-color="#bbb"/>
      </linearGradient>
    </defs>
    <!-- diagonal bands -->
    <polygon points="0,588 660,372 660,380 0,596" fill="#222"/>
    <polygon points="0,600 660,386 660,396 0,612" fill="#fff"/>
    <polygon points="0,612 660,396 660,700 0,700" fill="var(--red)"/>
    <!-- cover panel -->
    <rect x="660" y="373" width="323" height="6" fill="url(#rule)"/>
    <rect x="660" y="388" width="323" height="312" fill="var(--red)"/>
  </svg>

  <div class="fold" style="left:335px"></div>
  <div class="fold" style="left:660px"></div>

  <!-- inside flap -->
  <section class="panel panel--about">
    <div class="feature feature--quality">
      <span class="badge"><svg viewBox="0 0 52 52" aria-hidden="true"><path d="M15 19h4l3 12h12l3-9H21" fill="none" stroke="#fff" stroke-width="2.2" stroke-linejoin="round"/><circle cx="23" cy="35" r="2" fill="#fff"/><circle cx="33" cy="35" r="2" fill="#fff"/></svg></span>
      <h3>HIGH END</h3>
      <p>User freindly products</p>
    </div>
    <div class="feature feature--eco">
      <span class="badge"><svg viewBox="0 0 52 52" aria-hidden="true"><path d="M26 14c6 4 6 11 0 14-6-3-6-10 0-14zM16 32c2-6 8-8 12-5-2 5-8 7-12 5zM36 32c-2-6-8-8-12-5 2 5 8 7 12 5z" fill="#fff"/></svg></span>
      <h3>ECO FREINDLY</h3>
      <p>Materials</p>
    </div>

    <h2 class="about-title">WE ARE</h2>
    <ul class="about-list">
      <li>Brightmoor Works G.P,</li>
      <li>Canadian Furniture and Stationery Distributor (very attractive patented design -mainly Desks &amp; Chairs-)</li>
      <li>Adjstable to fit many needs.</li>
    </ul>

    <div class="photo photo--standing-desk" role="img" aria-label="Photo of a height-adjustable wooden standing desk on a white tripod base"></div>
  </section>

  <!-- middle panel -->
  <section class="panel panel--contact">
    <div class="brand brand--middle">
      <span class="dot"></span>
      <div><span class="name">Brightmoor Works G.P</span><span class="tag">Canadian furniture and stationery distributor</span></div>
    </div>

    <div class="claim">
      <span class="c1">VERY ATTRACTIVE</span>
      <span class="c2">patented design</span>
      <span class="c3">MAINLY</span>
      <span class="c4">DESKS &amp; CHAIRS</span>
    </div>

    <p class="phone">0123456789</p>
    <p class="web web--middle">www.companywebsite.com</p>
  </section>

  <!-- cover panel -->
  <section class="panel panel--cover">
    <div class="brand brand--cover">
      <span class="dot"></span>
      <div><span class="name">Brightmoor Works G.P</span><span class="tag">Canadian furniture and stationery distributor</span></div>
    </div>

    <div class="photo photo--study-desk" role="img" aria-label="Photo of a white adjustable children's study desk with tilting top"></div>

    <h1 class="cover-title">
      <span class="l1">CANADIAN</span>
      <span class="l2">FURNITURE</span>
      <span class="l3">and Stationery Distributor</span>
    </h1>
    <p class="web web--cover">www.companywebsite.com</p>
  </section>
</main>
</body>
</html>
```